logo/ product label

We handcraft and infuse organically grown herbs to create body products (lotions, massage oils, face creams and healing salves) and tinctures for resale and use in our massage therapy office on the harbor of Camden, Maine. Our new venture is called "Larkhollow Tide Company", and we like the idea of a vintage apothecary looking label and a logo that works well incorporating the sea, and our herbal healthy and pure product line. We have a tourist, yacht ...and local clientele.

Target Market(s)

clients wanting healthy products for their skin ,
tourists wanting to "bring it home" from their vacation

Industry/Entity Type

Product

Font styles to use
Decorative

Colors
fde08a
cadf82
faf289
acd036
33b7a4
fff3d0
fbc994
cfeae6

Requirements
Must have
• simple, understandable camden maine ocean vacation with handcrafted herbal products to bring home
• understated
Nice to have
• elegant and subtle /modern or vintage logo, to be shown on cobalt blue glass or aluminum tins
Should not have
• flashy, airbrushy,

```html
<!DOCTYPE html>
<html lang="en">
<head>
<meta charset="utf-8">
<title>Larkhollow Tide Company – Massage Oil Label</title>
<link rel="stylesheet" href="https://fonts.googleapis.com/css2?family=Cinzel:wght@500;600&family=IM+Fell+English&family=Pinyon+Script&display=swap">
<style>
  :root {
    --paper: #e8e2d6;
    --ink: #141414;
    --page: #ffffff;
    --art-light: #ddd6c8;
    --art-dark: #b9b2a5;
  }
  html, body {
    margin: 0;
    padding: 0;
    width: 1200px;
    height: 1200px;
    overflow: hidden;
    background: var(--page);
  }
  .label {
    display: block;
    width: 1200px;
    height: 1200px;
  }
  .label__field { fill: var(--paper); }
  .label__frame-heavy { fill: none; stroke: var(--ink); stroke-width: 12; }
  .label__frame-light { fill: none; stroke: var(--ink); stroke-width: 3; }
  .label__state {
    font-family: "IM Fell English", serif;
    font-size: 25px;
    letter-spacing: 4px;
    fill: var(--ink);
  }
  .label__company {
    font-family: "Cinzel", serif;
    font-weight: 600;
    font-size: 62px;
    letter-spacing: 5px;
    fill: var(--ink);
  }
  .label__product {
    font-family: "Pinyon Script", cursive;
    font-size: 150px;
    fill: var(--ink);
  }
  .label__arc-text {
    font-family: "Cinzel", serif;
    font-weight: 500;
    font-size: 40px;
    letter-spacing: 3px;
    fill: var(--ink);
  }
  .label__established {
    font-family: "IM Fell English", serif;
    font-size: 30px;
    fill: var(--ink);
  }
  .divider__rule { stroke: var(--ink); stroke-width: 2; }
  .divider__swell { fill: var(--ink); }
  .divider__bead { fill: none; stroke: var(--ink); stroke-width: 2; }
  .flourish { fill: var(--art-dark); }
</style>
</head>
<body>
<svg class="label" viewBox="0 0 1200 1200" xmlns="http://www.w3.org/2000/svg" aria-labelledby="label-title">
  <title id="label-title">Larkhollow Tide Company Massage Oil, Organic Infusions, Est. 2014</title>
  <defs>
    <linearGradient id="lighthouse-tone" x1="0" y1="0" x2="0" y2="1">
      <stop offset="0" stop-color="var(--art-dark)"/>
      <stop offset="1" stop-color="var(--art-light)"/>
    </linearGradient>
    <path id="arc-path" d="M 340 1010 A 260 260 0 0 1 860 1010"/>
  </defs>

  <!-- label body -->
  <polygon class="label__field" points="353,0 847,0 1200,353 1200,847 847,1200 353,1200 0,847 0,353"/>
  <polygon class="label__frame-heavy" points="374,50 826,50 1150,374 1150,826 826,1150 374,1150 50,826 50,374"/>
  <polygon class="label__frame-light" points="383,72 817,72 1128,383 1128,817 817,1128 383,1128 72,817 72,383"/>

  <!-- header -->
  <text class="label__state" x="600" y="160" text-anchor="middle">ME</text>
  <rect class="flourish" x="345" y="180" width="510" height="40" rx="6" role="img" aria-label="Curled scroll flourish beneath the state mark"/>

  <text class="label__company" x="600" y="322" text-anchor="middle">Larkhollow Tide</text>
  <text class="label__company" x="600" y="405" text-anchor="middle">Company</text>

  <!-- upper divider -->
  <g class="divider">
    <line class="divider__rule" x1="180" y1="462" x2="1020" y2="462"/>
    <path class="divider__swell" d="M 300 462 Q 420 455 555 462 Q 420 469 300 462 Z"/>
    <path class="divider__swell" d="M 900 462 Q 780 455 645 462 Q 780 469 900 462 Z"/>
    <circle class="divider__bead" cx="228" cy="462" r="4"/>
    <circle class="divider__bead" cx="275" cy="462" r="4"/>
    <circle class="divider__bead" cx="925" cy="462" r="4"/>
    <circle class="divider__bead" cx="972" cy="462" r="4"/>
  </g>
  <rect class="flourish" x="562" y="440" width="76" height="44" rx="6" role="img" aria-label="Small knotted ornament at the centre of the divider"/>

  <!-- product name -->
  <text class="label__product" x="600" y="630" text-anchor="middle">Massage Oil</text>

  <!-- lower divider -->
  <g class="divider">
    <line class="divider__rule" x1="180" y1="728" x2="1020" y2="728"/>
    <path class="divider__swell" d="M 300 728 Q 450 721 600 728 Q 450 735 300 728 Z"/>
    <path class="divider__swell" d="M 900 728 Q 750 721 600 728 Q 750 735 900 728 Z"/>
    <circle class="divider__bead" cx="228" cy="728" r="4"/>
    <circle class="divider__bead" cx="275" cy="728" r="4"/>
    <circle class="divider__bead" cx="925" cy="728" r="4"/>
    <circle class="divider__bead" cx="972" cy="728" r="4"/>
  </g>

  <!-- emblem -->
  <rect x="480" y="760" width="240" height="290" rx="8" fill="url(#lighthouse-tone)" role="img" aria-label="Pen sketch of a lighthouse on a rocky shore"/>

  <text class="label__arc-text">
    <textPath href="#arc-path" startOffset="2%">Organic</textPath>
  </text>
  <text class="label__arc-text" text-anchor="end">
    <textPath href="#arc-path" startOffset="98%">Infusions</textPath>
  </text>

  <text class="label__established" x="600" y="1100" text-anchor="middle">Est. 2014</text>
</svg>
</body>
</html>
```